Wordpress theme website for professionals working together

My partner and I are offering business services, my wife in the energy business as mainly as member of the board of commissioners. I am working as interim manager/consultant in the accounting and finance area. Both activities are connected in one company VELMOT BV (dutch ltd). We need a CV based website. Beside this we do some financial and accounting services.

Target Market(s)

small medium business

Font styles to use
Sans Serif

Colors

Designer to choose colors to be used in the design.

Requirements
Must have
• Pictures of both members.
• CLEAN AND SIMPLE
• I LIKE BLACK & WHITE
Nice to have
• I like design like this theme: http://theme.pruxelo-example.com/resume/

```html
<!DOCTYPE html>
<html lang="en">
<head>
<meta charset="utf-8">
<title>VELMOT BV – Pieter</title>
<link href="https://fonts.googleapis.com/css2?family=Montserrat:wght@400;600;700;800&family=Open+Sans:wght@400;600&display=swap" rel="stylesheet">
<style>
:root{
  --ink:#111;
  --text:#333;
  --muted:#777;
  --white:#fff;
  --paper:#f2f2f2;
  --band:#e6e6e6;
  --bar-bg:#c4c4c4;
  --bar-fill:#1c1c1c;
  --card:#222;
  --line:#cfcfcf;
}
*{box-sizing:border-box;margin:0;padding:0}
html,body{width:1200px;height:3766px;overflow:hidden}
body{font-family:"Open Sans",Arial,sans-serif;color:var(--text);background:var(--white);position:relative}
.abs{position:absolute}
h1,h2,h3,h4,.nav,.btn{font-family:"Montserrat",Arial,sans-serif}
.section{position:absolute;left:0;width:1200px}
.section-title{position:absolute;left:0;width:1200px;text-align:center;font-size:29px;font-weight:800;color:var(--ink);letter-spacing:.5px}
.section-intro{position:absolute;left:320px;width:560px;text-align:center;font-size:11.5px;line-height:21px;color:var(--text)}

/* header */
.site-header{top:0;height:68px;background:var(--white)}
.brand{left:173px;top:18px;font-size:25px;font-weight:400;color:var(--ink);letter-spacing:1px}
.nav{right:173px;top:27px;display:flex;gap:26px;font-size:11px;font-weight:600;letter-spacing:.6px;color:#555}
.nav .active{color:var(--ink);font-weight:700}

/* hero */
.hero{top:68px;height:554px;background:linear-gradient(90deg,#d9d9d9 0%,#ececec 35%,#e2e2e2 100%);overflow:hidden}
.hero-photo{left:590px;top:0;width:610px;height:554px;background:radial-gradient(ellipse at 55% 42%,#9a9a9a 0%,#5e5e5e 40%,#2c2c2c 75%,#1a1a1a 100%)}
.hero-fade{left:560px;top:0;width:80px;height:554px;background:linear-gradient(90deg,#e6e6e6,rgba(230,230,230,0))}
.hero-name{left:171px;top:130px;font-size:46px;font-weight:600;letter-spacing:3px;color:var(--ink)}
.hero-text{left:173px;top:206px;width:390px;font-size:11.5px;line-height:19.5px;color:#3a3a3a}
.signature{left:173px;top:389px;width:120px;height:40px;background:linear-gradient(90deg,#cfcfcf,#dedede)}

/* jobs */
.jobs{top:622px;height:533px;background:var(--white)}
.jobs .section-title{top:62px}
.jobs .section-title span{color:#7a7a7a}
.col-title{top:141px;font-size:16px;font-weight:700;color:var(--ink);letter-spacing:.4px}
.timeline-line{width:1px;background:var(--line)}
.job-sep{height:1px;background:var(--line)}
.job-title{font-family:"Montserrat",Arial,sans-serif;font-weight:600;font-size:14px;line-height:18px;color:var(--ink)}
.job-desc{font-size:10.5px;line-height:17px;color:var(--text)}
.dot{width:12px;height:12px;border:1.5px solid #999;border-radius:50%;background:var(--white)}

/* skills */
.skills{top:1155px;height:550px;background:var(--band)}
.skills .section-title{top:52px}
.skills .section-intro{top:114px}
.skill-label{font-family:"Montserrat",Arial,sans-serif;font-size:11px;font-weight:700;color:var(--ink);letter-spacing:.3px}
.skill-bar{width:380px;height:30px;background:var(--bar-bg);clip-path:polygon(0 0,355px 0,380px 50%,355px 100%,0 100%)}
.skill-fill{position:absolute;left:0;top:0;height:30px;background:var(--bar-fill)}
.skill-pct{position:absolute;top:0;line-height:30px;font-size:11px;font-weight:600;color:var(--ink)}

/* expertise */
.expertise{top:1705px;height:436px;background:linear-gradient(160deg,#1b1b1b 0%,#0b0b0b 50%,#151515 100%)}
.card{top:97px;height:269px;background:var(--card);text-align:center;color:#bbb}
.card .icon{height:60px;margin-top:40px;display:flex;align-items:center;justify-content:center}
.card h3{font-size:13px;font-weight:700;letter-spacing:1px;color:var(--white);margin-top:40px}
.card p{font-size:12.5px;line-height:20px;margin-top:10px}

/* portfolio */
.portfolio{top:2141px;height:751px;background:var(--white)}
.portfolio .section-title{top:62px}
.portfolio .section-intro{top:122px}
.shot{width:279px;height:226px}

/* contact */
.contact{top:2892px;height:584px;background:var(--paper)}
.notch{left:568px;top:0;width:0;height:0;border-left:32px solid transparent;border-right:32px solid transparent;border-top:24px solid var(--white)}
.contact .section-title{top:68px}
.contact .section-intro{top:122px}
.info-head{font-family:"Montserrat",Arial,sans-serif;font-size:15px;font-weight:600;color:var(--ink);display:flex;align-items:center;gap:10px}
.info-text{font-size:11.5px;line-height:17.5px;color:#555}
.field{left:545px;width:409px;height:35px;background:var(--white);border:1px solid #ddd;font-size:10.5px;color:#888;padding:10px 12px}
.btn{left:545px;top:461px;width:130px;height:31px;background:var(--ink);color:var(--white);font-size:10.5px;font-weight:700;letter-spacing:.6px;text-align:center;line-height:31px}

/* footer */
.site-footer{top:3476px;height:290px;background:#000;color:#aaa}
.foot-head{top:46px;font-size:17px;font-weight:600;color:var(--white)}
.foot-links{top:80px;font-size:10.5px;line-height:20px;list-style:none;color:#9a9a9a}
.newsletter{left:708px;top:73px;width:319px;height:31px;border-radius:16px;background:#e9e9e9;overflow:hidden}
.newsletter span{position:absolute;left:14px;top:8px;font-size:10px;color:#999}
.newsletter b{position:absolute;right:0;top:0;width:82px;height:31px;border-radius:16px;background:#2b2b2b;color:var(--white);font-family:"Montserrat",Arial,sans-serif;font-size:10.5px;font-weight:700;text-align:center;line-height:31px}
.social{left:708px;top:136px;display:flex;gap:18px;font-size:12px;font-weight:600;color:var(--white)}
.foot-rule{left:173px;top:226px;width:854px;height:1px;background:#2a2a2a}
.copyright{left:0;top:252px;width:1200px;text-align:center;font-size:10.5px;color:#bbb}
</style>
</head>
<body>

<header class="section site-header">
  <div class="abs brand">VELMOT BV</div>
  <nav class="abs nav">
    <span class="active">HOME</span><span>ELISE</span><span>SKILLS</span><span>EXPERIENCE</span><span>PORTFOLIO</span><span>EDUCATION</span><span>CONTACT</span>
  </nav>
</header>

<section class="section hero">
  <div class="abs hero-photo" role="img" aria-label="Black and white portrait photo of Pieter, smiling, wearing glasses and a dark jacket"></div>
  <div class="abs hero-fade"></div>
  <h1 class="abs hero-name">PIETER</h1>
  <p class="abs hero-text">Sed ut perspiciatis unde omnis iste natus error sit voluptatem accusantium doloremque laudantium, totam rem aperiam, eaque ipsa quae ab illo inventore veritatis et quasi architecto beatae vitae dicta sunt explicabo. Nemo enim ipsam voluptatem quia voluptas sit aspernatur aut odit aut fugit, sed quia consequuntur magni dolores eos qui ratione voluptatem sequi nesciunt. Neque porro quisquam est, qui dolorem ipsum quia dolor sit amet, consectetur.</p>
  <div class="abs signature" role="img" aria-label="Handwritten signature of Pieter"></div>
</section>

<section class="section jobs">
  <h2 class="section-title">PIETER <span>JOBS</span></h2>

  <h3 class="abs col-title" style="left:173px">ACTUAL JOBS</h3>
  <div class="abs timeline-line" style="left:324px;top:201px;height:261px"></div>
  <div class="abs job-sep" style="left:173px;top:274px;width:151px"></div>
  <div class="abs job-title" style="left:173px;top:215px">Advisor WKR</div>
  <div class="abs dot" style="left:318px;top:216px"></div>
  <p class="abs job-desc" style="left:354px;top:200px;width:215px">Sed ut perspiciatis unde omnis iste natus error sit voluptatem accusa ntiumdolor emque laudantium, totam rem.</p>
  <div class="abs job-title" style="left:173px;top:297px;width:140px">Advisor Wit &amp; Wijs</div>
  <div class="abs dot" style="left:318px;top:308px"></div>
  <p class="abs job-desc" style="left:354px;top:285px;width:215px">Sed ut perspiciatis unde omnis iste nats error sit voluptatem accusa ntiumdolor emque laudantium, totam rem</p>
  <p class="abs job-desc" style="left:354px;top:366px;width:215px">Sed ut perspiciatis unde omnis iste nats error sit voluptatem accusa ntiumdolor emque laudantium, totam rem.ed ugers piciatis unde omnis iste natus error sit voluptatem accusa ntiumdolor</p>

  <h3 class="abs col-title" style="left:632px">FINISHED JOBS</h3>
  <div class="abs timeline-line" style="left:783px;top:196px;height:266px"></div>
  <div class="abs job-sep" style="left:632px;top:274px;width:151px"></div>
  <div class="abs job-sep" style="left:632px;top:364px;width:151px"></div>
  <div class="abs job-title" style="left:632px;top:205px;width:130px">Controller a.i. WKR</div>
  <div class="abs dot" style="left:777px;top:216px"></div>
  <p class="abs job-desc" style="left:813px;top:196px;width:216px">Sed ut perspiciatis unde omnis iste natus error sit voluptatem accusa ntiumdolor emque laudantium, totam rem.</p>
  <div class="abs job-title" style="left:632px;top:293px;width:140px">Advisor Solvera Green</div>
  <div class="abs dot" style="left:777px;top:308px"></div>
  <p class="abs job-desc" style="left:813px;top:285px;width:216px">Sed ut perspiciatis unde omnis iste natus error sit voluptatem accusa ntiumdolor emque laudantium, totam rem.</p>
  <div class="abs job-title" style="left:632px;top:384px;width:130px">Financial director EDR</div>
  <div class="abs dot" style="left:777px;top:399px"></div>
  <p class="abs job-desc" style="left:813px;top:377px;width:216px">Sed ut perspiciatis unde omnis iste natus error sit voluptatem accusa ntiumdolor emque laudantium, totam rem.</p>
</section>

<section class="section skills">
  <h2 class="section-title">SKILLS</h2>
  <p class="section-intro">Sed ut perspiciatis unde omnis iste nius error sit voluptatem accusa ntiumdolor emque laudantium, totam remd ut perspiciatis unde omnis iste nats error sit voluptatem accusa ntiumdolor emque lauda</p>

  <div class="abs skill-label" style="left:173px;top:186px">ANNUAL REPORTING</div>
  <div class="abs skill-bar" style="left:173px;top:213px"><div class="skill-fill" style="width:286px"></div><span class="skill-pct" style="left:313px">80%</span></div>
  <div class="abs skill-label" style="left:173px;top:254px">FINANCIAL MONTHLY REPORTING</div>
  <div class="abs skill-bar" style="left:173px;top:281px"><div class="skill-fill" style="width:222px"></div><span class="skill-pct" style="left:313px">40%</span></div>
  <div class="abs skill-label" style="left:173px;top:324px">ACCOUNTING</div>
  <div class="abs skill-bar" style="left:173px;top:351px"><div class="skill-fill" style="width:326px"></div><span class="skill-pct" style="left:330px">90%</span></div>
  <div class="abs skill-label" style="left:173px;top:392px">FINANCIAL MANAGEMENT</div>
  <div class="abs skill-bar" style="left:173px;top:419px"><div class="skill-fill" style="width:245px"></div><span class="skill-pct" style="left:313px">70%</span></div>

  <div class="abs skill-label" style="left:642px;top:186px">PROJECT MANAGEMENT</div>
  <div class="abs skill-bar" style="left:642px;top:213px"><div class="skill-fill" style="width:245px"></div><span class="skill-pct" style="left:313px">70%</span></div>
  <div class="abs skill-label" style="left:642px;top:254px">TEAM PLAYER</div>
  <div class="abs skill-bar" style="left:642px;top:281px"><div class="skill-fill" style="width:300px"></div><span class="skill-pct" style="left:313px">80%</span></div>
  <div class="abs skill-label" style="left:642px;top:324px">TROUBLE SHOOTER</div>
  <div class="abs skill-bar" style="left:642px;top:351px"><div class="skill-fill" style="width:300px"></div><span class="skill-pct" style="left:313px">80%</span></div>
  <div class="abs skill-label" style="left:642px;top:392px">ETC.</div>
  <div class="abs skill-bar" style="left:642px;top:419px"><div class="skill-fill" style="width:150px"></div><span class="skill-pct" style="left:313px">30%</span></div>
</section>

<section class="section expertise">
  <div class="abs card" style="left:173px;width:271px">
    <div class="icon"><svg width="66" height="54" viewBox="0 0 66 54" fill="none" stroke="#fff" stroke-width="2"><path d="M33 10C25 4 14 3 4 5v40c10-2 21-1 29 5 8-6 19-7 29-5V5C52 3 41 4 33 10z"/><path d="M33 10v40"/></svg></div>
    <h3>EDUCATION</h3>
    <p>Kavro (RA)<br>Lyceum Noord</p>
  </div>
  <div class="abs card" style="left:459px;width:276px">
    <div class="icon"><svg width="60" height="60" viewBox="0 0 60 60" fill="none" stroke="#fff" stroke-width="2"><path d="M8 52l26-26M34 26l6-6 6 2 8-8-6-2 4-6-6 2-8 8 2 6"/><path d="M8 8l6-2 18 18-4 4L10 14z"/><path d="M30 30l20 20-4 4-20-20"/></svg></div>
    <h3>WORKED FOR</h3>
    <p>Brekel Advocaten &amp; Notarissen<br>Dorvane Audit</p>
  </div>
  <div class="abs card" style="left:755px;width:272px">
    <div class="icon"><svg width="66" height="52" viewBox="0 0 66 52" fill="none" stroke="#fff" stroke-width="2"><rect x="3" y="3" width="60" height="46"/><rect x="9" y="9" width="48" height="34"/><path d="M12 40l14-16 10 11 6-6 12 11"/><circle cx="44" cy="18" r="3"/></svg></div>
    <h3>OTHER</h3>
    <p>Fotography</p>
  </div>
</section>

<section class="section portfolio">
  <h2 class="section-title">PORTFOLIO</h2>
  <p class="section-intro">Sed ut perspiciatis unde omnis iste nius error sit voluptatem accusa ntiumdolor emque laudantium, totam remd ut perspiciatis unde omnis iste nats error sit voluptatem accusa ntiumdolor emque lauda</p>
  <div class="abs shot" style="left:173px;top:193px;background:linear-gradient(135deg,#3c4b5e,#8b7a66 60%,#d8d2c8)" role="img" aria-label="Photo of a team discussing charts over a table with coffee"></div>
  <div class="abs shot" style="left:459px;top:193px;background:linear-gradient(135deg,#dfe8f2,#7fa1c6 55%,#2f4d78)" role="img" aria-label="Photo of a businessman touching a rising bar chart"></div>
  <div class="abs shot" style="left:748px;top:193px;background:linear-gradient(135deg,#c4b7a4,#5f5a54 55%,#d9d4cb)" role="img" aria-label="Photo of hands working on a laptop and tablet"></div>
  <div class="abs shot" style="left:173px;top:432px;background:linear-gradient(135deg,#e6e9ec,#4a5866 50%,#1f2a35)" role="img" aria-label="Photo of a man in a suit holding a tablet"></div>
  <div class="abs shot" style="left:459px;top:432px;background:linear-gradient(135deg,#f3d9b5,#b88a63 45%,#3a3531)" role="img" aria-label="Photo of hands typing on a laptop in warm light"></div>
  <div class="abs shot" style="left:748px;top:432px;background:linear-gradient(135deg,#eef1f3,#9aa8b3 50%,#5c5148)" role="img" aria-label="Photo of two colleagues reviewing figures on a laptop"></div>
</section>

<section class="section contact">
  <div class="abs notch"></div>
  <h2 class="section-title">CONTACT</h2>
  <p class="section-intro">Sed ut perspiciatis unde omnis iste nius error sit voluptatem accusa ntiumdolor emque laudantium, totam remd ut perspiciatis unde omnis iste nats error sit voluptatem accusa ntiumdolor emque lauda</p>

  <div class="abs info-head" style="left:269px;top:205px"><svg width="14" height="18" viewBox="0 0 14 18" fill="none" stroke="#333" stroke-width="1.4"><path d="M7 17S1 10 1 6.5a6 6 0 0112 0C13 10 7 17 7 17z"/><circle cx="7" cy="6.5" r="2.2"/></svg>Address</div>
  <p class="abs info-text" style="left:269px;top:236px">VELMOT BV<br>Lorem Ipsum Lore dummy<br>Lindelaan 14 voorbeeld<br>0000 XX Voorbeeldstad</p>
  <div class="abs info-head" style="left:269px;top:343px"><svg width="18" height="13" viewBox="0 0 18 13" fill="none" stroke="#333" stroke-width="1.4"><rect x="1" y="1" width="16" height="11"/><path d="M1 1l8 6 8-6"/></svg>Email</div>
  <p class="abs info-text" style="left:269px;top:370px">info@pieter-example.com</p>
  <div class="abs info-head" style="left:269px;top:414px"><svg width="16" height="16" viewBox="0 0 16 16" fill="none" stroke="#333" stroke-width="1.4"><path d="M4 1l3 4-2 2c1 2 2 3 4 4l2-2 4 3-2 3C7 15 1 9 1 3z"/></svg>Phone</div>
  <p class="abs info-text" style="left:269px;top:441px">01234 555016, 01234 555015</p>

  <div class="abs field" style="top:195px">Name:</div>
  <div class="abs field" style="top:234px">Email:</div>
  <div class="abs field" style="top:276px">Phone:</div>
  <div class="abs field" style="top:321px;height:128px">Message:</div>
  <div class="abs btn">SUBMIT HERE</div>
</section>

<footer class="section site-footer">
  <h4 class="abs foot-head" style="left:173px">Company</h4>
  <ul class="abs foot-links" style="left:173px"><li>Sed ut perspiciatis</li><li>Unde omnis iste</li><li>Voluptatem</li><li>Accusantium</li><li>Doloremque</li><li>Laudantium</li></ul>
  <h4 class="abs foot-head" style="left:354px">About</h4>
  <ul class="abs foot-links" style="left:354px"><li>Sed ut perspiciatis</li><li>Unde omnis iste</li><li>Voluptatem</li><li>Accusantium</li><li>Doloremque</li><li>Laudantium</li></ul>
  <h4 class="abs foot-head" style="left:517px">Links</h4>
  <ul class="abs foot-links" style="left:517px"><li>Sed ut perspiciatis</li><li>Unde omnis iste</li><li>Voluptatem</li><li>Accusantium</li><li>Doloremque</li><li>Laudantium</li></ul>
  <h4 class="abs foot-head" style="left:708px">Newsletter</h4>
  <div class="abs newsletter"><span>Email</span><b>SIGN UP</b></div>
  <div class="abs social"><span>Kivo</span><span>Trelo</span><span>Linqa</span><span>Snapo</span></div>
  <div class="abs foot-rule"></div>
  <p class="abs copyright">© 2018 All Rights Are Reserved.Terms of Use | Privacy Policy</p>
</footer>

</body>
</html>
```